Awesome photographers card for an awesome new business

Double sided business card Black background and silver logo in middle on one side. Details on otherside. please keep it simple

Industry/Entity Type

Photographer

Contact Information for Business Card

Gerald Fenwick
0452817360
GeraldFenwickPhotography47@mailbox.test
www.GeraldFenwickPhotography.test.au
Instagram _Gerald_fenwick

Requirements
Must have
• My logo in Silver
• please use instagram logo instead of "Instagram"

```html
<!DOCTYPE html>
<html lang="en">
<head>
<meta charset="utf-8">
<title>Gerald Fenwick Photography – Business Card</title>
<link rel="stylesheet" href="https://fonts.googleapis.com/css2?family=Lato:wght@400;700&display=swap">
<style>
  :root {
    --stage: #2a2a2b;
    --card: #252a2e;
    --silver: #d9dcde;
    --silver-soft: #b9bdc0;
    --divider: #6d7378;
  }
  * { margin: 0; padding: 0; box-sizing: border-box; }
  html, body { width: 1200px; height: 880px; overflow: hidden; }
  body {
    background: var(--stage);
    font-family: "Lato", sans-serif;
    color: var(--silver);
    position: relative;
  }
  .card {
    position: absolute;
    width: 560px;
    height: 320px;
    background: var(--card);
    border-radius: 18px;
  }
  .card--front { left: 70px; top: 100px; }
  .card--back { left: 570px; top: 460px; }

  .brand {
    display: flex;
    align-items: center;
    gap: 14px;
    color: var(--silver);
    font-weight: 400;
    letter-spacing: 0.12em;
    text-transform: uppercase;
  }
  .brand__dot {
    border: 2px solid var(--silver);
    border-radius: 50%;
    flex: none;
  }
  .card--front .brand {
    position: absolute;
    left: 50%; top: 50%;
    transform: translate(-50%, -50%);
    font-size: 24px;
    white-space: nowrap;
  }
  .card--front .brand__dot { width: 30px; height: 30px; }

  .card--back .brand {
    position: absolute;
    left: 30px; top: 50%;
    transform: translateY(-50%);
    font-size: 15px;
    line-height: 1.35;
    gap: 10px;
  }
  .card--back .brand__dot { width: 20px; height: 20px; }

  .divider {
    position: absolute;
    left: 232px; top: 70px;
    width: 1px; height: 180px;
    background: var(--divider);
  }
  .details {
    position: absolute;
    left: 252px; top: 88px;
    right: 20px;
  }
  .details__name {
    font-weight: 700;
    font-size: 19px;
    letter-spacing: 0.02em;
    text-transform: uppercase;
    margin-bottom: 14px;
  }
  .details__list { list-style: none; }
  .details__item {
    display: flex;
    align-items: center;
    gap: 8px;
    font-size: 12.5px;
    color: var(--silver-soft);
    margin-bottom: 6px;
    white-space: nowrap;
  }
  .details__icon { width: 15px; height: 15px; flex: none; }
  .details__web {
    font-size: 12.5px;
    color: var(--silver-soft);
    margin-top: 14px;
  }
</style>
</head>
<body>
  <section class="card card--front" aria-label="Business card front">
    <div class="brand">
      <span class="brand__dot"></span>
      <span class="brand__name">Gerald Fenwick</span>
    </div>
  </section>

  <section class="card card--back" aria-label="Business card back">
    <div class="brand">
      <span class="brand__dot"></span>
      <span class="brand__name">Gerald<br>Fenwick</span>
    </div>
    <div class="divider"></div>
    <div class="details">
      <h1 class="details__name">Gerald Fenwick</h1>
      <ul class="details__list">
        <li class="details__item">
          <svg class="details__icon" viewBox="0 0 16 16" aria-hidden="true">
            <circle cx="8" cy="8" r="8" fill="#d9dcde"/>
            <path d="M5.2 4.2l1.4-.3.8 1.9-.9.7c.5 1.1 1.3 1.9 2.4 2.4l.7-.9 1.9.8-.3 1.4c-3.4.2-6.2-2.6-6-6z" fill="#252a2e"/>
          </svg>
          <span>0452817360</span>
        </li>
        <li class="details__item">
          <svg class="details__icon" viewBox="0 0 16 16" aria-hidden="true">
            <circle cx="8" cy="8" r="8" fill="#d9dcde"/>
            <rect x="4" y="5.2" width="8" height="5.6" rx="0.6" fill="#252a2e"/>
            <path d="M4.3 5.6L8 8.4l3.7-2.8" stroke="#d9dcde" stroke-width="0.9" fill="none"/>
          </svg>
          <span>GeraldFenwickPhotography47@mailbox.test</span>
        </li>
        <li class="details__item">
          <svg class="details__icon" viewBox="0 0 16 16" aria-hidden="true">
            <circle cx="8" cy="8" r="8" fill="#d9dcde"/>
          </svg>
          <span>_Gerald_fenwick</span>
        </li>
      </ul>
      <p class="details__web">www.GeraldFenwickPhotography.test.au</p>
    </div>
  </section>
</body>
</html>
```